Website Design for a Chemical Sales Company

We are working with a Chemical Sales Company in California. They sell various chemicals throughout the US.
Types of products they sell: https://www.wardenvale.example/us/products/all
https://www.molvista.example/products/kerrin/glacyn-glycol-thermal-fluids/glacyn-propylene-glycol-thermal-fluids
Some sites to use for inspiration:
https://www.molvista.example
https://www.kerrin.example/en-us
Thank you for taking the time to consider designing a website for us. We are web developers based in Stockton, CA, USA. Most of our projects go through the same process. Understanding this process may help you win a project with us. We custom-code all of our websites in-house. We don’t have any requirements as to what tools you use for your design, but we ask that you follow these guidelines.
IMAGES:
If you use any images or icons in the design, we ask that you have a link to the asset so we can purchase the image/icon. Most of the designs we submit do not have the customer’s images on them unless they have some great images. Be creative; show us the feeling you are trying to portray with your image choices. Use any royalty-free site you choose. We subscribe to Pelmora and mainly use their images, but we can purchase images outside of Pelmora. PLEASE NOTE: we will not submit designs to clients with watermarks on the images.
FONTS:
We ask that you identify the fonts you’re using in the design. This can be done in a message if you want. We typically use Google Fonts and Pelmora Fonts.
CONTENT:
We're always open to different content and ideas. We often submit designs with stock images so the client can see our vision. We typically take pictures after the website launch to use their images with our vision. Lorem Ipsum is fine for paragraphs, but we ask that you make the Headers with correct English. We want to be able to show the vision and identify the sections of the website.
INSPIRATION:
We typically add a couple of links in the brief of websites we like to help you get started in your design.
REVISIONS:
We do not often ask for revisions of the designs unless we see something in the design that may not appeal to the client. If there are slight changes that we want to make, we do that in the development process.
FEEDBACK:
We rarely give feedback on designs during the design process. We are working on many website projects and do not have the time to provide feedback. We usually respond if your request is well thought out and asks specific questions, but a note asking “feedback, please” usually goes unanswered.

```html
<!DOCTYPE html>
<html lang="en">
<head>
<meta charset="utf-8">
<title>Valencore — Chemical Sales</title>
<link href="https://fonts.googleapis.com/css2?family=Didact+Gothic&family=Montserrat:wght@400;500;600&display=swap" rel="stylesheet">
<style>
  :root{
    --brand:#0aa3e0;
    --ink:#1b1b1b;
    --white:#ffffff;
    --border:#444;
    --partner-bg:#ebedf0;
    --partner-ink:#1e2b4a;
    --footer-bg:#5b5f66;
    --footer-text:#e6e8ea;
  }
  *{margin:0;padding:0;box-sizing:border-box}
  html,body{width:1200px;height:2953px;overflow:hidden;background:var(--white)}
  body{position:relative;font-family:"Montserrat",sans-serif;color:var(--ink)}
  .display{font-family:"Didact Gothic",sans-serif;font-weight:400}
  a{color:inherit;text-decoration:none}

  /* header */
  .site-header{position:absolute;top:0;left:0;width:1200px;height:83px;background:var(--white);box-shadow:0 2px 6px rgba(0,0,0,.08);z-index:2}
  .brand{position:absolute;left:111px;top:30px;font-family:"Didact Gothic",sans-serif;font-size:22px;letter-spacing:.5px;color:#2a2f3a}
  .main-nav{position:absolute;left:300px;top:31px;display:flex;gap:34px;font-family:"Didact Gothic",sans-serif;font-size:17px}
  .main-nav .caret{display:inline-block;width:8px;height:8px;border-right:2px solid var(--ink);border-bottom:2px solid var(--ink);transform:rotate(45deg);margin-left:6px;position:relative;top:-3px}
  .search{position:absolute;left:672px;top:22px;width:223px;height:38px;border:1.5px solid var(--brand);border-radius:19px;display:flex;align-items:center;gap:8px;padding-left:14px;font-family:"Didact Gothic",sans-serif;font-size:17px}
  .btn{display:inline-flex;align-items:center;justify-content:center;border-radius:8px;font-family:"Didact Gothic",sans-serif;font-size:19px}
  .btn-solid{background:var(--brand);color:var(--white);box-shadow:0 2px 4px rgba(0,0,0,.2)}
  .btn-light{background:var(--white);color:var(--brand);box-shadow:0 1px 4px rgba(0,0,0,.15)}
  .contact-btn{position:absolute;left:970px;top:22px;width:119px;height:38px}

  /* hero */
  .hero{position:absolute;top:83px;left:0;width:1200px;height:514px}
  .hero-visual{position:absolute;inset:0;background:linear-gradient(100deg,#1d3f86 0%,#3b6cb4 25%,#8fc1ea 50%,#bfe1f7 70%,#7fb4e0 100%)}
  .hero-copy{position:absolute;left:145px;top:137px;width:435px;color:#0f1a2a}
  .hero-copy .kicker{font-size:27px;font-weight:600;color:var(--white)}
  .hero-copy h1{font-size:39px;color:var(--white);margin-top:4px;letter-spacing:.5px}
  .hero-copy p{font-size:15.5px;font-weight:500;line-height:26px;margin-top:16px;text-align:justify}
  .hero-copy .btn{width:118px;height:38px;margin-top:16px}

  /* products */
  .section-title{position:absolute;left:0;width:1200px;text-align:center;font-size:33px;color:var(--ink)}
  .product{position:absolute;top:757px;width:232px;height:259px;border:1.5px solid var(--border);text-align:center}
  .product.is-active{border:2.5px solid var(--brand)}
  .product .shot{width:120px;height:130px;margin:20px auto 0;border-radius:10px}
  .product h3{font-family:"Didact Gothic",sans-serif;font-weight:400;font-size:16px;margin-top:27px}
  .product a{display:inline-block;margin-top:10px;color:var(--brand);text-decoration:underline;font-family:"Didact Gothic",sans-serif;font-size:17px}
  .products-more{position:absolute;left:540px;top:1062px;width:118px;height:39px}

  /* about */
  .about{position:absolute;top:1187px;left:0;width:1200px;height:664px;background:linear-gradient(120deg,#e2f2fb,#cde9f6 60%,#dff0f8)}
  .about-visual{position:absolute;left:111px;top:183px;width:367px;height:367px;border-radius:50%;background:radial-gradient(circle at 45% 55%,#8a7fb0,#4e4566 70%)}
  .about-text{position:absolute;left:540px;top:178px;width:548px;font-size:16.5px;line-height:26px;color:#222}
  .about-text p{margin-bottom:9px}
  .about-text .btn{width:118px;height:38px;margin-top:27px}

  /* blog */
  .blog-card{position:absolute;top:2010px;width:468px;height:284px;color:var(--white)}
  .blog-card .cover{position:absolute;inset:0}
  .blog-card p{position:absolute;left:20px;top:205px;width:420px;font-size:17.5px;font-weight:500;line-height:26px}

  /* partners */
  .partners{position:absolute;top:2380px;left:0;width:1200px;height:294px;background:var(--partner-bg)}
  .partner-row{position:absolute;left:160px;top:140px;width:880px;display:flex;justify-content:space-between;align-items:center;font-weight:600;font-size:32px;color:var(--partner-ink)}
  .partner-row span{display:flex;align-items:center;gap:12px}
  .partner-row i{display:inline-block;width:30px;height:30px;background:var(--partner-ink)}
  .arrow{position:absolute;top:142px}

  /* footer */
  .site-footer{position:absolute;top:2674px;left:0;width:1200px;height:279px;background:var(--footer-bg);color:var(--footer-text)}
  .footer-col{position:absolute;top:54px;font-size:15.5px;line-height:26px}
  .footer-col h4{font-family:"Didact Gothic",sans-serif;font-weight:400;font-size:17px;margin-bottom:12px;color:var(--white)}
  .copyright{position:absolute;top:236px;left:0;width:1200px;text-align:center;font-size:15.5px}
</style>
</head>
<body>

<header class="site-header">
  <div class="brand">VALENCORE</div>
  <nav class="main-nav">
    <a href="#">Products<span class="caret"></span></a>
    <a href="#">Testimonials</a>
    <a href="#">About Us</a>
  </nav>
  <div class="search">
    <svg width="16" height="16" viewBox="0 0 16 16"><circle cx="6.5" cy="6.5" r="5" fill="none" stroke="#1b1b1b" stroke-width="2"/><line x1="10.3" y1="10.3" x2="15" y2="15" stroke="#1b1b1b" stroke-width="2"/></svg>
    <span>Search</span>
  </div>
  <a class="btn btn-solid contact-btn" href="#">Contact Us</a>
</header>

<section class="hero">
  <div class="hero-visual" role="img" aria-label="Glossy blue molecular structure floating over water"></div>
  <div class="hero-copy">
    <div class="kicker">WELCOME TO</div>
    <h1 class="display">VALENCORE</h1>
    <p>Lorem ipsum dolor sit amet, consectetur adipiselit, sed do eiusmod tempor incididunt ut labore et dolore magna aliqua.</p>
    <a class="btn btn-light" href="#">Learn More</a>
  </div>
</section>

<h2 class="section-title display" style="top:680px">OUR PRODUCTS</h2>

<article class="product" style="left:117px">
  <div class="shot" role="img" aria-label="White jerrycan of solar thermal fluid" style="background:linear-gradient(#f4f4f4,#d6d9de)"></div>
  <h3>K110 Solar Thermal Fluid</h3><a href="#">View More</a>
</article>
<article class="product is-active" style="left:361px">
  <div class="shot" role="img" aria-label="Two containers of solar cleaner" style="background:linear-gradient(#f2f4f7,#c9d2de)"></div>
  <h3>K210 Solar Cleaner</h3><a href="#">View More</a>
</article>
<article class="product" style="left:606px">
  <div class="shot" role="img" aria-label="Blue and green test kit case" style="background:linear-gradient(#2b58a8,#3a9a45)"></div>
  <h3>Clearflow Test Kit</h3><a href="#">View More</a>
</article>
<article class="product" style="left:850px">
  <div class="shot" role="img" aria-label="Teal bottle of system cleaner" style="background:linear-gradient(#e9f7f6,#5fd0c7)"></div>
  <h3>Wardenvale V400 Cleaner</h3><a href="#">View More</a>
</article>
<a class="btn btn-solid products-more" href="#">View More</a>

<section class="about">
  <h2 class="section-title display" style="top:86px">ABOUT US</h2>
  <div class="about-visual" role="img" aria-label="Laboratory flask with molecular shapes"></div>
  <div class="about-text">
    <p>Lorem ipsum dolor sit amet, consectetur adipiscing elit, sed do eiusmod tempor incididunt ut labore et dolore magna aliqua. Quis ipsum suspendisse ultrices gravida. Risus commodo viverra maecenas accumsan lacus vel facilisis.</p>
    <p>Lorem ipsum dolor sit amet, consectetur adipiscing elit, sed do eiusmod tempor incididunt ut labore et dolore magna aliqua. Quis ipsum suspendisse ultrices gravida. Risus commodo viverra maecenas accumsan lacus vel facilisis.</p>
    <p>Lorem ipsum dolor sit amet, consectetur adipiscing elit, sed do eiusmod tempor</p>
    <a class="btn btn-light" href="#">Learn More</a>
  </div>
</section>

<h2 class="section-title display" style="top:1932px">OUR BLOG</h2>
<article class="blog-card" style="left:111px">
  <div class="cover" role="img" aria-label="Electric car charging at night" style="background:linear-gradient(160deg,#2b3340,#0c0f14 70%)"></div>
  <p>Lorem ipsum dolor sit amet, consectetur adip elit, sed do eiusmod</p>
</article>
<article class="blog-card" style="left:620px">
  <div class="cover" role="img" aria-label="Chemical plant lit up at night" style="background:linear-gradient(160deg,#253b5c,#0f1726 70%)"></div>
  <p>Lorem ipsum dolor sit amet, consectetur adip elit, sed do eiusmod</p>
</article>

<section class="partners">
  <h2 class="section-title display" style="top:60px">PROUDLY PARTNERED WITH</h2>
  <svg class="arrow" style="left:108px" width="26" height="42" viewBox="0 0 26 42" aria-hidden="true"><path d="M22 3 L5 21 L22 39" fill="none" stroke="var(--brand)" stroke-width="4.5"/></svg>
  <div class="partner-row">
    <span>Solvane Chemical</span>
    <span><i></i>Brookmere</span>
    <span>Harrowfield</span>
  </div>
  <svg class="arrow" style="left:1066px" width="26" height="42" viewBox="0 0 26 42" aria-hidden="true"><path d="M4 3 L21 21 L4 39" fill="none" stroke="var(--brand)" stroke-width="4.5"/></svg>
</section>

<footer class="site-footer">
  <div class="footer-col" style="left:110px"><h4>RESOURCES</h4>MyAccount@Kerrin<br>Customer Support<br>Contact Us</div>
  <div class="footer-col" style="left:378px"><h4>EDUCATION</h4>News<br>Events</div>
  <div class="footer-col" style="left:605px"><h4>CORPORATE</h4>About<br>Careers<br>Investors<br>Build Together blog</div>
  <div class="footer-col" style="left:873px"><h4>LEGAL</h4>Privacy Statement<br>Terms of Use<br>Accessibility Statement<br>California Supply Chain Act</div>
  <div class="copyright">Copyrights 2023 Valencore.All Rights Reserved.</div>
</footer>

</body>
</html>
```